Corportate Power Point Template

We need a corporate PPT Design for our startup Big Data company.

Basically, our company will ingest, analyze and generate dynamic Dashboards with data consumed from different sources like Social Networks, Enterprise Legacy Systems such as e-Commerce, ERP, CRM and others.

Company is headquartered in Brazil, but will have a global presence.

Industry/Entity Type

It Company

```html
<!DOCTYPE html>
<html lang="en">
<head>
<meta charset="utf-8">
<title>Project Title Here – About Us</title>
<link rel="stylesheet" href="https://fonts.googleapis.com/css2?family=Exo+2:wght@400;500;600&family=Roboto+Condensed:wght@400&display=swap">
<style>
  :root {
    --orange: #fd7430;
    --orange-text: #f2762e;
    --ink: #3a3a3a;
    --body-ink: #1e1410;
    --white: #ffffff;
    --page: #fdfbfb;
    --photo-light: #efe2ec;
    --photo-mid: #c7a7c3;
    --photo-dark: #8d6b8a;
  }
  * { margin: 0; padding: 0; box-sizing: border-box; }
  html, body { width: 1200px; height: 900px; overflow: hidden; background: var(--page); }
  .slide {
    position: relative;
    width: 1200px;
    height: 900px;
    overflow: hidden;
    background: var(--page);
    font-family: "Exo 2", sans-serif;
  }
  .slide-header {
    position: absolute;
    left: 0; top: 0;
    width: 1200px; height: 136px;
    background: var(--white);
  }
  .header-accent {
    position: absolute;
    left: 0; top: 32px;
    width: 14px; height: 76px;
    background: var(--orange);
  }
  .slide-title {
    position: absolute;
    left: 36px; top: 28px;
    font-size: 52px;
    font-weight: 500;
    line-height: 1.2;
    color: var(--ink);
    letter-spacing: 0.5px;
  }
  .slide-title .highlight { color: var(--orange-text); }
  .about-panel {
    position: absolute;
    left: 0; top: 136px;
    width: 568px; height: 682px;
    background: var(--orange);
  }
  .panel-pointer {
    position: absolute;
    left: 566px; top: 440px;
    width: 28px; height: 50px;
  }
  .about-heading {
    position: absolute;
    left: 56px; top: 336px;
    font-size: 62px;
    font-weight: 400;
    color: var(--white);
    line-height: 1;
  }
  .about-body {
    position: absolute;
    left: 56px; top: 408px;
    width: 474px;
    font-size: 21px;
    font-weight: 500;
    line-height: 28.5px;
    color: var(--body-ink);
    text-align: justify;
    text-align-last: left;
  }
  .office-photo {
    position: absolute;
    left: 568px; top: 136px;
    width: 632px; height: 682px;
    background: linear-gradient(170deg, var(--photo-light) 0%, var(--photo-mid) 55%, var(--photo-dark) 100%);
  }
  .slide-footer {
    position: absolute;
    left: 0; top: 818px;
    width: 1200px; height: 82px;
    background: var(--white);
  }
  .presenter {
    position: absolute;
    left: 12px; top: 36px;
    font-family: "Roboto Condensed", sans-serif;
    font-size: 20px;
    color: var(--ink);
  }
  .presenter .presenter-name { color: var(--orange-text); }
  .brand {
    position: absolute;
    right: 16px; top: 22px;
    display: flex;
    align-items: center;
    gap: 10px;
  }
  .brand-mark {
    width: 22px; height: 22px;
    background: var(--orange);
  }
  .brand-name {
    font-size: 36px;
    font-weight: 500;
    color: var(--orange-text);
    line-height: 1;
  }
</style>
</head>
<body>
<main class="slide">
  <header class="slide-header">
    <div class="header-accent"></div>
    <h1 class="slide-title"><span class="highlight">Project</span> Title Here</h1>
  </header>

  <section class="about-panel" aria-labelledby="about-heading"></section>
  <div class="office-photo" role="img" aria-label="Photo of a bright open-plan office with white desks and mesh chairs"></div>
  <svg class="panel-pointer" viewBox="0 0 28 50" aria-hidden="true">
    <polygon points="0,0 28,25 0,50" fill="var(--orange)"/>
  </svg>
  <h2 class="about-heading" id="about-heading">ABOUT US</h2>
  <p class="about-body">Lorem ipsum dolor sit Lorem ipsum dolor sit Lorem ipsum dolor sit Lorem ipsum dolor sit Lorem ipsum dolor sit Lorem ipsum dolor sit</p>

  <footer class="slide-footer">
    <p class="presenter">Persentatator Name : <span class="presenter-name">Marina Velloso</span></p>
    <div class="brand">
      <span class="brand-mark"></span>
      <span class="brand-name">Vantora Labs</span>
    </div>
  </footer>
</main>
</body>
</html>
```